Hello my name is Colin, I am Starting a business called Lumen Wellness and fitness and am in need of a memorable business card.
It is a personal training studio. I have added the logo that i would like to be on the left center om my business card. i would like room left up the top for a heading sentence such as. "Is your body shocking for all the wrong reasons". there must be room left on the right of the logo below the main heading for 3 sub headings.
then under those 3 headings and logo room for another larger heading eg. "give me a call and learn how to eat chocolate, drink bear and have great sex". in what room is left i would like to be used for my contact details, use I'm Colin Ferrante your fitness expert on the left then on the right Phone, Email and website space in at least 12 Point. Very specific i know :) now onto the back, for the back i would like an eye catching graphic and room for one main headline and 3 bullet points centered just write anything i will choose what to put in them when i pick a winner. Thank you very much for sticking through all of that :) i appreciate you taking the time to read it and hopefully undergo designing me a business card.
I can't wait to see the designs!

Target Market(s)

slightly more towards females although it would probably be best if it was targeted towards both sexes

Industry/Entity Type

Training

Requirements
Nice to have
• I would love to see if anyone could come up with a design that would really make my card stand out and be memorable.
Should not have
• tacky fitness photos of abs and muscles etc.

```html
<!DOCTYPE html>
<html lang="en">
<head>
<meta charset="utf-8">
<title>Lumen Wellness and fitness – business cards</title>
<link href="https://fonts.googleapis.com/css2?family=Questrial&family=Open+Sans:wght@400&display=swap" rel="stylesheet">
<style>
  :root {
    --stage: #e7e4df;
    --card: #ffffff;
    --ink: #333333;
    --ink-soft: #4a4a4a;
    --brand: #1b4f8f;
    --brand-deep: #0f3a6e;
    --brand-light: #2a63a8;
    --block: #333333;
    --white: #ffffff;
  }
  * { box-sizing: border-box; margin: 0; padding: 0; }
  html, body { width: 1200px; height: 788px; overflow: hidden; }
  body {
    position: relative;
    background: var(--stage);
    font-family: "Questrial", "Century Gothic", sans-serif;
    color: var(--ink);
  }
  .view-label {
    position: absolute;
    font-family: "Open Sans", Arial, sans-serif;
    font-size: 21px;
    color: var(--ink);
    transform: translateX(-50%);
    white-space: nowrap;
  }
  .card {
    position: absolute;
    width: 524px;
    height: 300px;
    background: var(--card);
    border-radius: 20px;
    overflow: hidden;
    box-shadow: 0 4px 14px rgba(0,0,0,0.18);
  }
  .card--front { left: 338px; top: 74px; }
  .card--back-one { left: 54px; top: 446px; }
  .card--back-two { left: 621px; top: 442px; }

  .abs { position: absolute; white-space: nowrap; }

  .tagline { font-size: 13px; color: var(--ink); }

  .brand-name { color: var(--brand); line-height: 1; font-weight: 400; }
  .brand-sub { color: var(--brand-deep); line-height: 1; font-weight: 400; text-align: right; }

  /* front */
  .front-block { left: 0; top: 87px; width: 57px; height: 57px; background: var(--block); }
  .front-band {
    left: 274px; top: 87px; width: 250px; height: 57px;
    background: linear-gradient(90deg, var(--brand-deep), var(--brand-light));
    color: var(--white); text-align: right; padding: 10px 30px 0 0;
  }
  .front-band .person-name { font-size: 17px; line-height: 1.2; }
  .front-band .person-role { font-size: 12px; line-height: 1.4; }
  .front-logo { left: 64px; top: 84px; }
  .front-logo .brand-name { font-size: 58px; }
  .front-logo .brand-sub { font-size: 16px; margin-top: 2px; }

  .contact-list { left: 58px; top: 190px; list-style: none; font-family: "Open Sans", Arial, sans-serif; }
  .contact-list li { display: flex; align-items: center; height: 31px; color: var(--ink); font-size: 21px; }
  .contact-list li:first-child { font-size: 23px; }
  .contact-list svg { width: 14px; height: 14px; margin-right: 8px; flex: none; }

  .promo { right: 25px; top: 224px; text-align: right; font-size: 13px; line-height: 17.5px; color: var(--ink-soft); }

  /* back one */
  .figure-art {
    left: 42px; top: 20px; width: 140px; height: 262px;
    border-radius: 40px 40px 10px 10px;
    background: linear-gradient(90deg, var(--brand-deep), var(--brand-light));
  }
  .back-one-logo { left: 254px; top: 22px; }
  .back-one-logo .brand-name { font-size: 34px; }
  .back-one-logo .brand-sub { font-size: 10px; margin-top: 1px; }
  .bullets { left: 258px; top: 116px; list-style: none; font-family: "Open Sans", Arial, sans-serif; font-size: 16px; color: var(--ink); }
  .bullets li { position: relative; padding-left: 25px; height: 34px; }
  .bullets li::before { content: ""; position: absolute; left: 0; top: 8px; width: 6px; height: 6px; background: var(--ink); }
  .back-one-web { left: 256px; top: 252px; font-family: "Open Sans", Arial, sans-serif; font-size: 20px; color: var(--ink); }

  /* back two */
  .back-two-tagline { left: 0; width: 524px; top: 19px; text-align: center; }
  .back-two-logo { left: 0; width: 524px; top: 78px; text-align: center; }
  .back-two-logo .brand-name { font-size: 86px; }
  .back-two-logo .brand-sub { font-size: 22px; margin-top: 6px; text-align: center; }
  .back-two-web { left: 0; width: 524px; top: 251px; text-align: center; font-size: 20px; letter-spacing: 4px; color: var(--ink); }
</style>
</head>
<body>
  <div class="view-label" style="left:600px; top:32px;">Front</div>
  <div class="view-label" style="left:323px; top:403px;">Back - 1</div>
  <div class="view-label" style="left:897px; top:403px;">Back - 2</div>

  <section class="card card--front">
    <p class="abs tagline" style="left:28px; top:37px;">Is your body shocking for all the wrong reasons</p>
    <div class="abs front-block"></div>
    <div class="abs front-logo">
      <div class="brand-name">Lumen</div>
      <div class="brand-sub">Wellness and fitness</div>
    </div>
    <div class="abs front-band">
      <div class="person-name">Colin Ferrante</div>
      <div class="person-role">Your Fitness Expert</div>
    </div>
    <ul class="abs contact-list">
      <li>
        <svg viewBox="0 0 16 16"><circle cx="8" cy="8" r="7" fill="none" stroke="#333" stroke-width="1.3"/><path d="M5.5 4.5l1.5 1.5-1 1.2a6 6 0 0 0 2.8 2.8l1.2-1 1.5 1.5-1.2 1.2C7.6 11.5 4.5 8.4 4.3 5.7z" fill="#333"/></svg>
        +12 555 01890
      </li>
      <li>
        <svg viewBox="0 0 16 16"><path d="M1 6l7-4 7 4v8H1z" fill="#333"/><path d="M3 7l5 3 5-3" fill="none" stroke="#fff" stroke-width="1.2"/></svg>
        info@lumenfit.co
      </li>
      <li>
        <svg viewBox="0 0 16 16" fill="none" stroke="#333" stroke-width="1.1"><circle cx="8" cy="8" r="6.5"/><ellipse cx="8" cy="8" rx="3" ry="6.5"/><path d="M1.5 8h13M2.5 4.8h11M2.5 11.2h11"/></svg>
        www.lumenfit.co
      </li>
    </ul>
    <p class="abs promo">Give me a call and learn<br>how to eat chocolate, drink<br>bear and have great sex</p>
  </section>

  <section class="card card--back-one">
    <div class="abs figure-art" role="img" aria-label="Illustration area: blue silhouettes of a man in a suit and a woman standing side by side"></div>
    <div class="abs back-one-logo">
      <div class="brand-name">Lumen</div>
      <div class="brand-sub">Wellness and fitness</div>
    </div>
    <ul class="abs bullets">
      <li>Lorem Ipsum has been ...</li>
      <li>Lorem Ipsum has been ...</li>
      <li>Lorem Ipsum has been ...</li>
    </ul>
    <p class="abs back-one-web">www.lumenfit.co</p>
  </section>

  <section class="card card--back-two">
    <p class="abs tagline back-two-tagline">Is your body shocking for all the wrong reasons</p>
    <div class="abs back-two-logo">
      <div class="brand-name">Lumen</div>
      <div class="brand-sub">Wellness and fitness</div>
    </div>
    <p class="abs back-two-web">www.lumenfit.co</p>
  </section>
</body>
</html>
```